Business card for a Exhibition booth fabrication company

Hi. My company would like to change our corporate name card. We are an events and Exhibition stand builder company. We would like our corporate name card to resonate what we do. I need someone to create something unique that relates to the industry that I am in. The graphic designer should be creative to incorporate the elements of my industry and try to blend in well in the design of the card. Our aim is to ensure that we are unique and our card can look different from our competitors.
Updates

Target Market(s)

Marketing and events manager from all companies

Contact Information for Business Card

The business card should have the following details:
Name
Job Title
Email
Website

Colors

Designer to choose colors to be used in the design.

Requirements
Must have
• The card must be look something that is relevant to the service that I am providing. My website is: www.velmora-buildworks.com
• You can see my website to get more information on what service that I am doing
Nice to have
• On the back of my card, I would like to have a globe image with the incorporation of my company logo. This is to indicate that my services can be done in any part of the world.

```html
<!DOCTYPE html>
<html lang="en">
<head>
<meta charset="utf-8">
<title>Velmora Buildworks – Business Card</title>
<link href="https://fonts.googleapis.com/css2?family=Work+Sans:wght@400;500&family=Josefin+Sans:wght@600&display=swap" rel="stylesheet">
<style>
  :root {
    --backdrop: #2b2b2b;
    --card-white: #ffffff;
    --card-grey: #5f6062;
    --brand-red: #e3262b;
    --text-grey: #5a5a5a;
    --text-light: #f2f2f2;
  }
  * { box-sizing: border-box; margin: 0; padding: 0; }
  html, body { width: 1200px; height: 900px; overflow: hidden; }
  body {
    background: var(--backdrop);
    font-family: "Work Sans", sans-serif;
    display: flex;
    flex-direction: column;
    align-items: center;
    justify-content: center;
    gap: 44px;
  }
  .card {
    width: 640px;
    height: 366px;
    border-radius: 22px;
    position: relative;
    overflow: hidden;
    box-shadow: 0 10px 30px rgba(0,0,0,.45);
  }
  /* Front */
  .card--front {
    background: var(--card-white);
    display: flex;
    align-items: center;
    padding: 0 40px 0 44px;
  }
  .brand-block {
    width: 250px;
    display: flex;
    align-items: center;
    gap: 12px;
  }
  .brand-dot {
    width: 26px; height: 26px;
    border-radius: 50%;
    background: var(--brand-red);
    flex: none;
  }
  .brand-name {
    font-family: "Josefin Sans", sans-serif;
    font-weight: 600;
    font-size: 22px;
    line-height: 1.2;
    letter-spacing: 2px;
    color: var(--brand-red);
  }
  .divider {
    width: 1.5px;
    height: 190px;
    background: var(--brand-red);
    margin: 0 26px 0 14px;
  }
  .details { color: var(--text-grey); }
  .person-name {
    font-size: 27px;
    font-weight: 500;
    color: var(--brand-red);
    letter-spacing: .5px;
    text-transform: uppercase;
  }
  .person-title { font-size: 17px; margin: 2px 0 10px; }
  .address { font-size: 15px; line-height: 1.3; margin-bottom: 6px; }
  .contact-list { list-style: none; font-size: 15px; line-height: 1.45; }
  .contact-list li { display: flex; align-items: center; gap: 8px; }
  .contact-list svg { width: 11px; height: 11px; flex: none; }
  /* Back */
  .card--back {
    background: var(--card-grey);
    display: flex;
    align-items: center;
    justify-content: center;
    gap: 16px;
  }
  .card--back .brand-dot { width: 34px; height: 34px; }
  .card--back .brand-name {
    color: var(--text-light);
    font-size: 30px;
    letter-spacing: 4px;
  }
</style>
</head>
<body>
  <section class="card card--front">
    <div class="brand-block">
      <span class="brand-dot"></span>
      <span class="brand-name">VELMORA<br>BUILDWORKS</span>
    </div>
    <div class="divider"></div>
    <div class="details">
      <h1 class="person-name">Daniel Harlow</h1>
      <p class="person-title">Director</p>
      <p class="address">P.O. Box 4182 Palm Crest<br>Avenue Lusail - Qatar</p>
      <ul class="contact-list">
        <li><svg viewBox="0 0 12 12"><path d="M2 1l2 0 1 3-1.5 1a6 6 0 0 0 3 3L7.5 7l3 1v2c0 .6-.5 1-1 1A9 9 0 0 1 1 2c0-.5.4-1 1-1z" fill="var(--brand-red)"/></svg>+65 81704426</li>
        <li><svg viewBox="0 0 12 12"><rect x="3" y="0.5" width="6" height="11" rx="1.2" fill="none" stroke="var(--brand-red)" stroke-width="1.3"/><circle cx="6" cy="9.5" r=".8" fill="var(--brand-red)"/></svg>+974 55128840</li>
        <li><svg viewBox="0 0 12 12"><rect x="0.7" y="2.2" width="10.6" height="7.6" fill="none" stroke="var(--brand-red)" stroke-width="1.3"/><path d="M1 2.6l5 4 5-4" fill="none" stroke="var(--brand-red)" stroke-width="1.3"/></svg>info@velmora-buildworks.com</li>
        <li><svg viewBox="0 0 12 12"><circle cx="6" cy="6" r="5.3" fill="none" stroke="var(--brand-red)" stroke-width="1.2"/><path d="M.8 6h10.4M6 .7c-3 3.3-3 7.3 0 10.6M6 .7c3 3.3 3 7.3 0 10.6" fill="none" stroke="var(--brand-red)" stroke-width="1"/></svg>www.velmora-buildworks.com</li>
      </ul>
    </div>
  </section>

  <section class="card card--back">
    <span class="brand-dot"></span>
    <span class="brand-name">VELMORA BUILDWORKS</span>
  </section>
</body>
</html>
```